Roofing company in Toronto, Canada needs a logo design and business card design

We need a business card and logo created for our company. Our company is "KLV Roofing" which provides roofing services for commercial and residential customers. We serve customers in the Greater Toronto Area (in Canada) thus the name KLV.

We want the logo and business card to be a modern design displaying professionalism and quality in the work. We would prefer rounded corners for the business cards but are open to other ideas. The cards should be pleasant and appealing to customers.

Target Market(s)

Commercial and Residential customers

Industry/Entity Type

Roofing

Contact Information for Business Card

Logo Text

KLV Roofing

Requirements
Nice to have
• Colours that are pleasing to the eye but at the same time should stand out from other business cards. If the design can incorporate the name of KLV Roofing and the actual concept of roofing that would be nice.
Should not have
• Do not want the business cards or logo to be childish looking. Need to look professionally designed.

```html
<!DOCTYPE html>
<html lang="en">
<head>
<meta charset="utf-8">
<title>KLV Roofing — Business Card</title>
<link rel="stylesheet" href="https://fonts.googleapis.com/css2?family=Open+Sans:wght@400;600;700&display=swap">
<style>
  :root {
    --stage: #000000;
    --card-blue: #0b5b91;
    --card-grey: #878787;
    --ink-light: #ffffff;
    --brand-blue: #0d5c94;
  }
  * { margin: 0; padding: 0; box-sizing: border-box; }
  html, body { width: 1200px; height: 900px; overflow: hidden; background: var(--stage); }
  body { position: relative; font-family: "Open Sans", Arial, sans-serif; color: var(--ink-light); }

  .card { position: absolute; top: 275px; width: 477px; height: 293px; }
  .card--front {
    left: 116px; background: var(--card-blue);
    border-radius: 0 46px 0 46px;
  }
  .card--back {
    left: 622px; top: 276px; height: 292px; background: var(--card-grey);
    border-radius: 46px 0 46px 0;
  }

  .wordmark { position: absolute; font-weight: 700; letter-spacing: 0.5px; white-space: nowrap; line-height: 1; }
  .card--front .wordmark { left: 36px; top: 84px; font-size: 44px; color: var(--ink-light); }
  .card--back .wordmark { left: 0; right: 0; top: 122px; text-align: center; font-size: 48px; color: var(--brand-blue); }

  .identity { position: absolute; right: 19px; top: 35px; text-align: right; }
  .identity__name { font-weight: 700; font-size: 18.5px; line-height: 22px; }
  .identity__title { font-size: 13px; line-height: 17px; }

  .address { position: absolute; right: 21px; top: 157px; text-align: right; font-size: 13px; line-height: 17px; }

  .contacts { position: absolute; right: 20px; top: 217px; list-style: none; font-size: 13px; line-height: 17.5px; }
  .contacts li { display: flex; justify-content: flex-end; align-items: center; gap: 7px; }
  .contacts svg { width: 10px; height: 10px; fill: var(--ink-light); flex: none; }
</style>
</head>
<body>
  <section class="card card--front">
    <div class="wordmark">KLV Roofing</div>
    <div class="identity">
      <p class="identity__name">Daniel Reyes</p>
      <p class="identity__title">Managing Director</p>
    </div>
    <address class="address" style="font-style:normal">
      12345, Address Goes Here<br>Country Name, 123456
    </address>
    <ul class="contacts">
      <li>044-987 654 321
        <svg viewBox="0 0 10 10" aria-hidden="true"><path d="M2 0.5 L3.6 2.6 L2.8 3.6 Q4 6 6.4 7.2 L7.4 6.4 L9.5 8 L8.4 9.5 Q3.5 9 0.5 1.6 Z"/></svg>
      </li>
      <li>info@yourmail.com
        <svg viewBox="0 0 10 10" aria-hidden="true"><path d="M0.5 2 H9.5 V8 H0.5 Z M1.2 2.6 L5 5.4 L8.8 2.6" stroke="#0b5b91" stroke-width="0.7"/></svg>
      </li>
      <li>www.yoursitename.com
        <svg viewBox="0 0 10 10" aria-hidden="true" style="fill:none;stroke:#fff;stroke-width:1.2"><rect x="4.2" y="0.9" width="3.4" height="5" rx="1.7" transform="rotate(45 5.9 3.4)"/><rect x="2.4" y="4.1" width="3.4" height="5" rx="1.7" transform="rotate(45 4.1 6.6)"/></svg>
      </li>
    </ul>
  </section>

  <section class="card card--back">
    <div class="wordmark">KLV Roofing</div>
  </section>
</body>
</html>
```